Online interactive tutorial for year 2 to year 12 students in Australia

Website design for a new online tutorial for year 2 to year 12 students in Australia.

- The tutorial will be conducted via live webcam and within a dedicated interactive space
- The tutorial will be provided by high scoring undergraduates studying in top Australian universities.
- The tutors will be going through interviews & assessments & only top students are allowed to apply.
- Parents will do search and select tutor and have short 15 mins video interaction with potential tutors before booking them for their children for tutoring.
- hourly cost of booking (no monthly subscription or no hour limits)
- Tutors will have their own profile

Please see the attached for detailed page functionality.

The look and feel of the design must consider the following:
- must be educational but not dull and should stand out
- must appeal to younger generation - tutees (8-18 years), tutors (19-25), parents (30-50).
- Ideas for Logos (brivora.com.au but not confirmed)

Target Market(s)

tutees (8-18 years), tutors (19-25 years), parents (30-50 years).

Industry/Entity Type

Education

Coding

Coded - Design and coding required

Number of Pages Required

5+ page

Font styles to use
Serif

Requirements
Must have
• The look and feel of the design must consider the following:
• - must be educational but not dull and should stand out
• - must appeal to younger generation - tutees (8-18 years), tutors (19-25), parents (30-50).
Should not have
• Dullness

```html
<!DOCTYPE html>
<html lang="en">
<head>
<meta charset="utf-8">
<title>Brivora – Online Training for Children</title>
<link href="https://fonts.googleapis.com/css2?family=Roboto+Slab:wght@400&family=Raleway:wght@400;500;600;700&family=Open+Sans:wght@400;600;700&display=swap" rel="stylesheet">
<style>
:root{
  --navy:#1f4e8c;
  --navy-deep:#1a3f78;
  --footer:#2a5a9c;
  --footer-bar:#234d88;
  --green:#8cc63f;
  --green-dark:#6fae22;
  --orange:#ff8200;
  --orange-title:#f26a10;
  --text:#8a8a8a;
  --light:#f7f7f7;
  --white:#ffffff;
}
*{margin:0;padding:0;box-sizing:border-box}
html,body{width:1200px;height:2171px;overflow:hidden}
body{position:relative;background:var(--white);font-family:"Open Sans",sans-serif;color:var(--text)}
.abs{position:absolute}

/* header */
.brand{left:155px;top:28px;font-family:"Roboto Slab",serif;font-size:42px;color:var(--navy);line-height:1}
.register-btn{left:812px;top:45px;width:214px;height:36px;border-radius:18px;background:var(--navy);color:var(--white);
  font-size:14px;font-weight:600;display:flex;align-items:center;justify-content:center;gap:9px}
.nav{left:0;top:98px;width:1200px;height:51px;background:linear-gradient(#9ad14a,var(--green-dark));}
.nav ul{list-style:none;display:flex;position:absolute;left:156px;top:0;height:51px}
.nav li{height:51px;display:flex;align-items:center;padding:0 15px;color:var(--white);font-family:"Raleway",sans-serif;font-size:16.5px;font-weight:500;border-right:1px solid rgba(255,255,255,.3)}
.nav li:last-child{border-right:none}
.nav li.active{background:var(--navy);padding:0 22px}

/* hero */
.hero{left:0;top:149px;width:1200px;height:475px;background:linear-gradient(100deg,#6e8a6b 0%,#d9b49a 35%,#c89070 55%,#e8b0a8 75%,#7d8fa8 100%)}
.hero-caption{left:109px;top:376px;width:486px;height:142px;background:rgba(31,78,140,.82);padding:18px 46px;color:var(--white);font-family:"Raleway",sans-serif;font-weight:700}
.hero-caption .l1{font-size:44px;line-height:1.05}
.hero-caption .l2{font-size:36px;line-height:1.2}
.dots{left:562px;top:589px;display:flex;gap:5px}
.dots span{width:15px;height:15px;border-radius:50%;background:var(--white)}
.dots span.off{background:transparent;border:2px solid var(--white)}

/* about */
.about-band{left:0;top:624px;width:1200px;height:398px;background:var(--light)}
.section-title{font-family:"Raleway",sans-serif;font-weight:500;font-size:29px}
.about-title{left:174px;top:688px;color:var(--navy)}
.about-text{left:174px;top:744px;width:455px;font-size:13.5px;line-height:21px}
.about-text p{margin-bottom:14px}
.read-more{left:175px;top:913px;width:115px;height:35px;background:var(--navy-deep);color:var(--white);font-size:11.5px;font-weight:700;display:flex;align-items:center;justify-content:center;border-radius:2px}
.how-title{left:670px;top:682px;color:var(--orange-title)}
.video{left:672px;top:728px;width:370px;height:220px;background:linear-gradient(120deg,#7a7f86,#c9a27a 45%,#e3c06a 70%,#a89d8f)}
.video-bar{left:0;bottom:0;width:370px;height:28px;background:#2a2a2a}

/* services */
.services{left:0;top:1022px;width:600px;height:460px;background:var(--orange)}
.services-photo{left:600px;top:1022px;width:600px;height:460px;background:linear-gradient(110deg,#dfe6ec 0%,#c98f7c 35%,#e36a6a 60%,#f0d8c8 100%)}
.services-title{left:171px;top:1073px;color:var(--white);font-size:28px}
.service-list{left:171px;top:1131px;width:370px;list-style:none;color:var(--white);font-size:12px;line-height:18px}
.service-list li{display:flex;gap:9px;margin-bottom:14px}
.service-list svg{flex:none;margin-top:2px}

/* cards */
.card{top:1537px;width:284px;height:223px;color:var(--white);text-align:center;padding-top:50px;border-radius:2px}
.card.parents{left:162px;background:linear-gradient(135deg,rgba(40,95,170,.92),rgba(31,78,140,.95))}
.card.tutor{left:463px;background:linear-gradient(135deg,#9bd34a,#86c33a)}
.card.student{left:764px;background:linear-gradient(135deg,#ff8a1e,#ff6a00);padding-top:52px}
.card h3{font-family:"Raleway",sans-serif;font-weight:500;font-size:21px;line-height:27px;margin-bottom:6px}
.card p{font-size:11px;line-height:19px;padding:0 28px}
.card .btn{display:inline-block;margin-top:14px;border:2px solid var(--white);padding:5px 20px;font-size:12.5px}

/* footer */
.footer{left:0;top:1860px;width:1200px;height:253px;background:var(--footer);color:var(--white)}
.fcol{position:absolute;top:50px;font-size:11px;line-height:23px}
.fcol h4{font-family:"Raleway",sans-serif;font-weight:500;font-size:16px;margin-bottom:7px}
.fcol ul{list-style:none}
.fdiv{position:absolute;top:60px;width:1px;height:130px;background:rgba(255,255,255,.15)}
.contact-line{display:flex;align-items:center;gap:6px}
.socials{display:flex;gap:5px;margin-top:12px}
.socials span{width:29px;height:29px;border:1.5px solid var(--white);border-radius:50%}
.footer-bar{left:0;top:2113px;width:1200px;height:58px;background:var(--footer-bar);color:#c9d6ea;font-size:11px;display:flex;align-items:center;justify-content:center}
</style>
</head>
<body>

<div class="abs brand">Brivora</div>
<div class="abs register-btn">
  <svg width="16" height="16" viewBox="0 0 16 16"><circle cx="8" cy="5" r="3.5" fill="#9fc2ee"/><path d="M1.5 15c0-4 3-6 6.5-6s6.5 2 6.5 6z" fill="#9fc2ee"/></svg>
  Student Registration
</div>

<nav class="abs nav">
  <ul>
    <li class="active">Home</li><li>About Us</li><li>Services</li><li>Parents Registration</li><li>Tutor Registration</li><li>Payment</li><li>Contact Us</li>
  </ul>
</nav>

<div class="abs hero" role="img" aria-label="Children gathered around a laptop with a smiling teacher"></div>
<div class="abs hero-caption"><div class="l1">ONLINE TRAINING</div><div class="l2">FOR CHILDRENS</div></div>
<div class="abs dots"><span class="off"></span><span></span><span></span><span></span></div>

<section class="abs about-band"></section>
<h2 class="abs section-title about-title">About Us</h2>
<div class="abs about-text">
  <p>Donec quis mi sed magna hendrerit accumsan Suspendisse risus nibh ultricies eu volutpat non condimentum hendrerit augue</p>
  <p>Etiam eleifend metus vitae adipiscing semper mauris ipsum iaculis elit congue gravida elit mi egestas orci Curabitur pede Maecenas aliquet velit vel turpis Mauris neque metus malesuada nec ultricies</p>
  <p>Curabitur metus ipsum luctus eu malesuada ut tincidunt</p>
</div>
<div class="abs read-more">READ MORE</div>
<h2 class="abs section-title how-title">How it Works</h2>
<div class="abs video" role="img" aria-label="Video of a father and mother helping their child study">
  <svg class="abs" style="left:158px;top:73px" width="54" height="54" viewBox="0 0 54 54"><circle cx="27" cy="27" r="24" fill="rgba(0,0,0,.25)" stroke="#fff" stroke-width="3"/><path d="M21 16l17 11-17 11z" fill="#fff"/></svg>
  <div class="abs video-bar">
    <svg width="370" height="28" viewBox="0 0 370 28"><path d="M9 9l9 5-9 5z" fill="#fff"/><rect x="28" y="12" width="300" height="4" rx="2" fill="#ddd"/><rect x="28" y="12" width="100" height="4" rx="2" fill="#3a7bd5"/><path d="M340 11h4l4-3v12l-4-3h-4z" fill="#fff"/><path d="M352 10q3 4 0 8" stroke="#fff" fill="none"/></svg>
  </div>
</div>

<section class="abs services"></section>
<div class="abs services-photo" role="img" aria-label="Mother and daughter smiling at a tablet"></div>
<h2 class="abs section-title services-title">Our Services</h2>
<ul class="abs service-list">
  <li><svg width="15" height="15" viewBox="0 0 15 15"><circle cx="7.5" cy="7.5" r="7.5" fill="#fff"/><path d="M4 7.5l2.5 2.5 4.5-5" stroke="#ff8200" stroke-width="2" fill="none"/></svg><span>The tutorial will be conducted via live webcam and within a dedicated interactive space</span></li>
  <li><svg width="15" height="15" viewBox="0 0 15 15"><circle cx="7.5" cy="7.5" r="7.5" fill="#fff"/><path d="M4 7.5l2.5 2.5 4.5-5" stroke="#ff8200" stroke-width="2" fill="none"/></svg><span>The tutorial will be provided by high scoring undergraduates studying in top Australian universities.</span></li>
  <li><svg width="15" height="15" viewBox="0 0 15 15"><circle cx="7.5" cy="7.5" r="7.5" fill="#fff"/><path d="M4 7.5l2.5 2.5 4.5-5" stroke="#ff8200" stroke-width="2" fill="none"/></svg><span>The tutors will be going through interviews &amp; assessments &amp; only top students are allowed to apply.</span></li>
  <li><svg width="15" height="15" viewBox="0 0 15 15"><circle cx="7.5" cy="7.5" r="7.5" fill="#fff"/><path d="M4 7.5l2.5 2.5 4.5-5" stroke="#ff8200" stroke-width="2" fill="none"/></svg><span>Parents will do search and select tutor and have short 15 mins video interaction with potential tutors before booking them for their children for tutoring.</span></li>
  <li><svg width="15" height="15" viewBox="0 0 15 15"><circle cx="7.5" cy="7.5" r="7.5" fill="#fff"/><path d="M4 7.5l2.5 2.5 4.5-5" stroke="#ff8200" stroke-width="2" fill="none"/></svg><span>Hourly cost of booking (no monthly subscription or no hour limits)</span></li>
  <li><svg width="15" height="15" viewBox="0 0 15 15"><circle cx="7.5" cy="7.5" r="7.5" fill="#fff"/><path d="M4 7.5l2.5 2.5 4.5-5" stroke="#ff8200" stroke-width="2" fill="none"/></svg><span>Tutors will have their own profile</span></li>
</ul>

<div class="abs card parents" role="img" aria-label="Parent with child at a desk, tinted blue">
  <h3>PARENTS</h3>
  <p>Praesent elementum elit at tellus nec ultricies sit amet porttitor mattis enim In massa libero interdum nec</p>
  <span class="btn">Learn More</span>
</div>
<div class="abs card tutor" role="img" aria-label="Tutor working with a student, tinted green">
  <h3>TUTOR</h3>
  <p>Praesent elementum elit at tellus nec ultricies sit amet porttitor mattis enim In massa libero interdum nec</p>
  <span class="btn">Learn More</span>
</div>
<div class="abs card student" role="img" aria-label="Student studying, tinted orange">
  <h3>STUDENT<br>REGISTRATION</h3>
  <p>Praesent elementum elit at tellus nec ultricies sit amet porttitor mattis</p>
  <span class="btn">Learn More</span>
</div>

<footer class="abs footer">
  <div class="fcol" style="left:152px"><h4>COMPANY</h4><ul><li>Home</li><li>About Us</li><li>Why Us</li><li>Registration</li></ul></div>
  <div class="fdiv" style="left:270px"></div>
  <div class="fcol" style="left:302px"><h4>SUBLINKS</h4><ul><li>Curabitur metus</li><li>Apsum luctus</li><li>Eu malesuada</li><li>Pt tincidunt</li></ul></div>
  <div class="fdiv" style="left:431px"></div>
  <div class="fcol" style="left:465px"><h4>SUPPORT</h4><ul><li>Our Partners</li><li>Career</li><li>Term of Use</li><li>Contact Us</li></ul></div>
  <div class="fdiv" style="left:592px"></div>
  <div class="fcol" style="left:658px"><h4>RESOURCES</h4><ul><li>Parents Registration</li><li>Testimonials</li><li>Students</li><li>Tutor Profiles</li></ul></div>
  <div class="fcol" style="left:859px"><h4>CONTACT INFO</h4>
    <div>14 Harbour Lane Suite 5</div>
    <div class="contact-line"><svg width="12" height="12" viewBox="0 0 12 12"><path d="M2.5 1l2 2.5-1.2 1.2a7 7 0 0 0 4 4l1.2-1.2 2.5 2-1.5 1.5C5 11 1 7 1 2.5z" fill="none" stroke="#fff"/></svg>(02) 5550 0142</div>
    <div class="contact-line"><svg width="13" height="10" viewBox="0 0 13 10"><rect width="13" height="10" fill="#fff"/><path d="M0 0l6.5 5 6.5-5" stroke="#2a5a9c" fill="none"/></svg>info@brivora.com.au</div>
    <div class="socials"><span></span><span></span><span></span><span></span></div>
  </div>
</footer>
<div class="abs footer-bar">© 2016 Company Name&nbsp; All right reserved</div>

</body>
</html>
```